Company director needs a business card design

I am a semi-retired former senior finance executive who sits on a number of public and private company boards and do some consulting work. I work largely with emerging businesses but deal regularly with top end of town lawyers, bankers etc. I need a thoughtful but relatively conservative design which would also resonate with my younger client base. Some colour would be good. Information limited to name, address, office tel, mobile and email.

Finance

```html
<!DOCTYPE html>
<html lang="en">
<head>
<meta charset="utf-8">
<title>Business Card – Jonathan Doe</title>
<link rel="stylesheet" href="https://fonts.googleapis.com/css2?family=Exo+2:wght@400;500&display=swap">
<style>
  :root {
    --page-bg: #e6e6e6;
    --card-bg: #434343;
    --accent: #bfd54f;
    --text-light: #ffffff;
  }
  * { margin: 0; padding: 0; box-sizing: border-box; }
  html, body {
    width: 992px;
    height: 1200px;
    overflow: hidden;
    background: var(--page-bg);
    font-family: "Exo 2", sans-serif;
  }
  .canvas {
    position: relative;
    width: 992px;
    height: 1200px;
  }
  .card {
    position: absolute;
    left: 67px;
    top: 375px;
    width: 862px;
    height: 490px;
    background: var(--card-bg);
    border-radius: 26px;
    color: var(--text-light);
  }
  .identity {
    position: absolute;
    right: 494px;
    top: 181px;
    text-align: right;
    white-space: nowrap;
  }
  .identity__name {
    font-size: 34px;
    font-weight: 500;
    letter-spacing: 0.6px;
    line-height: 1;
    color: var(--accent);
  }
  .identity__role {
    font-size: 15px;
    font-weight: 500;
    line-height: 1;
    margin-top: 5px;
  }
  .identity__address {
    font-size: 21px;
    font-weight: 400;
    font-style: normal;
    letter-spacing: 1.5px;
    line-height: 25px;
    margin-top: 22px;
  }
  .divider {
    position: absolute;
    left: 418px;
    top: 133px;
    width: 2px;
    height: 232px;
    background: var(--accent);
  }
  .contacts {
    position: absolute;
    left: 473px;
    top: 180px;
    list-style: none;
    white-space: nowrap;
  }
  .contacts__item {
    display: flex;
    align-items: center;
    height: 32.5px;
    font-size: 20px;
    letter-spacing: 0.6px;
  }
  .contacts__icon {
    flex: none;
    width: 22px;
    height: 22px;
    margin-right: 14px;
    fill: none;
    stroke: var(--text-light);
    stroke-width: 2;
  }
</style>
</head>
<body>
<main class="canvas">
  <section class="card" aria-label="Business card">
    <div class="identity">
      <h1 class="identity__name">JONATHAN DOE</h1>
      <p class="identity__role">Managing Director</p>
      <address class="identity__address">
        Address your Inc 00 2nd Ave<br>
        Ashford, NJ xxxxx
      </address>
    </div>

    <div class="divider"></div>

    <ul class="contacts">
      <li class="contacts__item">
        <svg class="contacts__icon" viewBox="0 0 22 22" aria-hidden="true">
          <rect x="5" y="2" width="12" height="18" rx="2"/>
          <line x1="10" y1="17" x2="12" y2="17"/>
        </svg>
        0012 3456 789
      </li>
      <li class="contacts__item">
        <svg class="contacts__icon" viewBox="0 0 22 22" aria-hidden="true">
          <rect x="6" y="2" width="10" height="18"/>
          <line x1="11" y1="2" x2="11" y2="20"/>
          <line x1="6" y1="7" x2="16" y2="7"/>
          <line x1="6" y1="11" x2="16" y2="11"/>
          <line x1="6" y1="15" x2="16" y2="15"/>
          <line x1="3" y1="20.5" x2="19" y2="20.5"/>
        </svg>
        0012 3456 789
      </li>
      <li class="contacts__item">
        <svg class="contacts__icon" viewBox="0 0 22 22" aria-hidden="true">
          <rect x="1" y="4" width="20" height="14"/>
          <polyline points="1,4 11,12 21,4"/>
          <line x1="1" y1="18" x2="8" y2="10"/>
          <line x1="21" y1="18" x2="14" y2="10"/>
        </svg>
        info@yourmail.com
      </li>
      <li class="contacts__item">
        <svg class="contacts__icon" viewBox="0 0 22 22" aria-hidden="true">
          <rect x="1" y="3" width="20" height="13"/>
          <line x1="11" y1="16" x2="11" y2="19"/>
          <line x1="7" y1="20" x2="15" y2="20"/>
        </svg>
        www.yourwebsite.com
      </li>
    </ul>
  </section>
</main>
</body>
</html>
```